Business Cards for a law firm

Business cards for our law firm. Use our silhoette logo and OAK PARTNERS - check our website (www.oakpartners.example)

Contact Information for Business Card

our silhouette logo, OAK PARTNERS, 800-555-0147, Dorian Pemberton, dorian@oakpartners.example

Requirements
Must have
• our silhouette logo, OAK PARTNERS, 800-555-0147, Dorian Pemberton, dorian@oakpartners.example

```html
<!DOCTYPE html>
<html lang="en">
<head>
<meta charset="utf-8">
<title>Oak Partners — Business Cards</title>
<link rel="stylesheet" href="https://fonts.googleapis.com/css2?family=Cinzel:wght@600;700&family=Arimo:wght@400&display=swap">
<style>
  :root {
    --backdrop: #e6e7ea;
    --card-white: #ffffff;
    --navy: #1b2f6b;
    --navy-light: #2a4286;
    --gold: #f2a51f;
    --ink-white: #ffffff;
  }
  * { box-sizing: border-box; margin: 0; padding: 0; }
  html, body {
    width: 1200px; height: 874px; overflow: hidden;
    background: var(--backdrop);
  }
  .canvas {
    position: relative; width: 1200px; height: 874px;
  }
  .card {
    position: absolute; left: 280px; width: 640px; height: 366px;
    border-radius: 26px; overflow: hidden;
    box-shadow: 0 10px 28px rgba(0,0,0,0.18);
  }
  .card--front { top: 51px; background: var(--card-white); }
  .card--back { top: 457px; background: var(--navy); }

  .brand {
    position: absolute; left: 150px; top: 150px;
    display: flex; align-items: center; gap: 18px;
  }
  .brand__mark {
    width: 44px; height: 44px; background: var(--navy);
  }
  .brand__name {
    font-family: "Cinzel", serif; font-weight: 700;
    font-size: 34px; letter-spacing: 4px; color: var(--navy);
  }

  .figure {
    position: absolute; background: linear-gradient(180deg, var(--navy-light), #233a7c);
    border-radius: 40px 40px 6px 6px;
  }
  .figure--left { left: 40px; top: 40px; width: 150px; height: 300px; }
  .figure--right { right: 40px; top: 110px; width: 150px; height: 240px; }

  .details {
    position: absolute; left: 190px; right: 190px; top: 120px;
    text-align: center; color: var(--ink-white);
  }
  .details__firm {
    font-family: "Cinzel", serif; font-weight: 700;
    font-size: 25px; letter-spacing: 3px;
  }
  .details__person {
    margin-top: 10px;
    font-family: "Cinzel", serif; font-weight: 700;
    font-size: 21px; letter-spacing: 1.5px; color: var(--gold);
  }
  .details__rule {
    width: 30px; height: 1px; background: var(--ink-white);
    margin: 10px auto 10px;
  }
  .details__contact {
    font-family: "Arimo", sans-serif; font-size: 15px; line-height: 1.35;
    list-style: none;
  }
</style>
</head>
<body>
<main class="canvas">
  <section class="card card--front" aria-label="Card front">
    <div class="brand">
      <span class="brand__mark" aria-hidden="true"></span>
      <span class="brand__name">OAK PARTNERS</span>
    </div>
  </section>

  <section class="card card--back" aria-label="Card back">
    <div class="figure figure--left" role="img" aria-label="Standing figure silhouette illustration"></div>
    <div class="figure figure--right" role="img" aria-label="Standing figure silhouette illustration"></div>
    <div class="details">
      <p class="details__firm">OAK PARTNERS</p>
      <p class="details__person">Dorian Pemberton</p>
      <div class="details__rule" aria-hidden="true"></div>
      <ul class="details__contact">
        <li>800-555-0147</li>
        <li>dorian@oakpartners.example</li>
        <li>www.oakpartners.example</li>
      </ul>
    </div>
  </section>
</main>
</body>
</html>
```